Our Premium Canadian Organic Hemp Oil needs a clean, modern label design!

Design a label for organic hemp oil bottle. Max three colours. Clean white background. The over all style and concept needs to work for future products and other packaging. As an example, hemp seed, or beverage.
Bottle is 2 1/4 inches in diameter and 9 inches from bottom to the neck, 11 inches in total. 500ml.
The design is Clean, simple, sophisticated, modern label design. We would like a simple botanical drawing of hemp plant and seeds (no buds).
Certiva Bio symbol - see below
Vegan symbol
Paleo

The back of the bottle should have the following description below and the nutritional data provided in the attachments.
“This is Vela Tundris
In our quest to find foods with the highest purity, nutritional density, and sustainability, we discovered and fell in love with the pristine Boreal region of Quebec. This land is protected by the beautiful Laurentian Mountain Ranges and is known to produce plants of particularly high nutritional composition.
The natural harmony of the Boreal region and its ecosystem protects the vegetation from a variety of common pests and diseases. These natural barriers removes the need for impurities such as GMOs and harmful sprays.

Nourish from Within!
Our hemp oil quenches thirsty cells with abundant essential fatty acids that alleviate dry skin, hair and nails, boosts metabolism and immunity, and regulates hormones and blood pressure.

Try on salads, drizzle on pasta, garnish dips, add to smoothies or take by the tablespoon.
“Goodness by the spoonful”

“Part of a healthy and balanced diet” above the nutritional data chart

Target Market(s)

Canada & USA, Products for consumers seeking superior quality product from artisan farms.

Font styles to use
Serif
Sans Serif
Decorative

Colors

Designer to choose colors to be used in the design.

Requirements
Must have
• The design is for the front sticker label, we will award the winning designer with the extended works to do the back sticker and the additional products. We like the fonts and spacing used by the Orrin & Pell brand, provided below as inspiration.
• Brand name: “Vela Tundris”
• Slogan: “Finely crafted hemp foods”
• “Cold pressed Organic Hemp Oil”
• Brief Description: “Luxurious locks & radiant skin, beauty comes from within.
• Our artisan organic hemp oil quenches thirsty cells with full spectrum plant based Omega 3 & 6”
• Certiva Bio symbol - see below
• Vegan symbol
• Paleo
Nice to have
• We like the Orrin & Pell sticker seal and imagine “N 48” in the circle of the sticker and “Organically Yours” written on the length of the seal sticker.
Should not have
• We want our product to stand out from the competitors so we are vearing away from the styling of other brands.

```html
<!DOCTYPE html>
<html lang="en">
<head>
<meta charset="utf-8">
<title>Vela Tundris – Cold Pressed Organic Hemp Oil Label</title>
<link href="https://fonts.googleapis.com/css2?family=Gilda+Display&family=Lora:ital,wght@0,500;0,600;1,400;1,600&display=swap" rel="stylesheet">
<style>
  :root {
    --backdrop: #ececec;
    --label-white: #ffffff;
    --hemp-green: #8aab47;
    --ink-grey: #6e6e6e;
    --ink-dark: #2f2f2f;
    --icon-dark: #3a4a22;
    --on-green: #ffffff;
  }
  * { margin: 0; padding: 0; box-sizing: border-box; }
  html, body {
    width: 1134px;
    height: 1200px;
    overflow: hidden;
    background: var(--backdrop);
  }
  .label {
    position: absolute;
    left: 291px;
    top: 50px;
    width: 552px;
    height: 1100px;
    background: var(--label-white);
    overflow: hidden;
  }
  .label__band {
    position: absolute;
    left: 0;
    top: 627px;
    width: 100%;
    bottom: 0;
    background: var(--hemp-green);
  }
  .brand-box {
    position: absolute;
    left: 75px;
    top: 105px;
    width: 293px;
    height: 66px;
    border: 2px solid var(--ink-grey);
    display: flex;
    align-items: center;
    justify-content: center;
  }
  .brand-name {
    font-family: "Gilda Display", serif;
    font-size: 43px;
    color: var(--ink-grey);
    line-height: 1;
    letter-spacing: 0.5px;
    white-space: nowrap;
  }
  .tagline {
    position: absolute;
    left: 75px;
    top: 204px;
    font-family: "Lora", serif;
    font-style: italic;
    font-weight: 400;
    font-size: 27px;
    line-height: 30px;
    letter-spacing: 3.5px;
    color: var(--ink-dark);
  }
  .botanical {
    position: absolute;
    left: 81px;
    top: 318px;
    width: 443px;
    height: 412px;
    border-radius: 40% 45% 35% 50%;
    background: radial-gradient(ellipse at 55% 45%, rgba(150,150,150,0.22) 0%, rgba(170,170,170,0.10) 55%, rgba(200,200,200,0) 75%);
  }
  .product-title {
    position: absolute;
    left: 94px;
    top: 720px;
    font-family: "Lora", serif;
    font-weight: 600;
    font-size: 24px;
    line-height: 29px;
    letter-spacing: 1px;
    color: var(--on-green);
    text-transform: uppercase;
  }
  .product-copy {
    position: absolute;
    left: 91px;
    top: 808px;
    font-family: "Lora", serif;
    font-style: italic;
    font-weight: 600;
    font-size: 21.5px;
    line-height: 26.5px;
    letter-spacing: 0.6px;
    color: var(--on-green);
  }
  .volume {
    position: absolute;
    left: 91px;
    top: 1004px;
    padding-left: 12px;
    border-left: 4px solid var(--on-green);
    font-family: "Lora", serif;
    font-style: italic;
    font-weight: 600;
    font-size: 22px;
    line-height: 34px;
    color: var(--on-green);
  }
  .diet-badge {
    position: absolute;
    width: 80px;
    text-align: center;
  }
  .diet-badge svg { display: block; margin: 0 auto; }
  .diet-badge__caption {
    margin-top: 6px;
    font-family: "Lora", serif;
    font-weight: 500;
    font-size: 13px;
    letter-spacing: 0.5px;
    color: var(--icon-dark);
  }
  .diet-badge--paleo { left: 397px; top: 770px; }
  .diet-badge--vegan { left: 401px; top: 870px; }
  .certification-seal {
    position: absolute;
    left: 401px;
    top: 966px;
    width: 80px;
    height: 76px;
  }
</style>
</head>
<body>
  <main class="label">
    <div class="label__band"></div>

    <div class="botanical" role="img" aria-label="Fine line botanical drawing of a hemp plant with serrated leaves"></div>

    <div class="brand-box"><span class="brand-name">Vela Tundris</span></div>
    <p class="tagline">Finely crafted<br>hemp foods</p>

    <h1 class="product-title">Cold Pressed<br>Organic Hemp Oil</h1>
    <p class="product-copy">Our artisan organic<br>hemp oil quenches<br>thirsty cells with full<br>spectrum plant based<br>Omega 3 &amp; 6</p>
    <p class="volume">500ml</p>

    <div class="diet-badge diet-badge--paleo">
      <svg width="64" height="64" viewBox="0 0 64 64" aria-hidden="true">
        <circle cx="32" cy="32" r="29" fill="none" stroke="var(--icon-dark)" stroke-width="2.5"/>
        <path d="M32 14 L44 30 L36 30 L40 44 L24 44 L28 30 L20 30 Z" fill="none" stroke="var(--icon-dark)" stroke-width="2"/>
        <line x1="12" y1="12" x2="52" y2="52" stroke="var(--icon-dark)" stroke-width="2.5"/>
      </svg>
      <div class="diet-badge__caption">PALEO</div>
    </div>

    <div class="diet-badge diet-badge--vegan">
      <svg width="64" height="64" viewBox="0 0 64 64" aria-hidden="true">
        <circle cx="32" cy="32" r="29" fill="none" stroke="var(--icon-dark)" stroke-width="2.5"/>
        <path d="M30 48 C16 44 16 28 24 20 C28 30 32 36 30 48 Z" fill="var(--icon-dark)"/>
        <path d="M33 48 C34 32 40 24 48 18 C50 34 44 44 33 48 Z" fill="var(--icon-dark)"/>
      </svg>
      <div class="diet-badge__caption">VEGAN</div>
    </div>

    <svg class="certification-seal" viewBox="0 0 80 76" role="img" aria-label="Certification seal">
      <ellipse cx="40" cy="38" rx="36" ry="34" fill="var(--icon-dark)" opacity="0.85"/>
    </svg>
  </main>
</body>
</html>
```